Brightwave Reach - Business Card

We need a business card for a Social Media Marketing company that specializes in online marketing for small businesses in Canada using common Social Media platforms such as Pixlora, Chatterly, Blinkpost & Quibber.

I have uploaded a copy of our logo which I would like utilized in the business card. We would like the business card to be modern yet classy design.

Our website is www.brightwavereach.ca

Industry/Entity Type

Marketing

Contact Information for Business Card

Email: info@brightwavereach.ca
Website: www.brightwavereach.ca
Telephone: 604-555-0193

Colors

Designer to choose colors to be used in the design.

Requirements
Must have
• Social Media icons on reverse
• Please add some designs with color.

```html
<!DOCTYPE html>
<html lang="en">
<head>
<meta charset="utf-8">
<title>Brightwave Reach – Business Card</title>
<link href="https://fonts.googleapis.com/css2?family=Open+Sans:wght@400;600;700;800&display=swap" rel="stylesheet">
<style>
  :root {
    --backdrop: #d9d9d9;
    --paper: #f5efe0;
    --paper-edge: #ece2cc;
    --ink: #3a3a3a;
    --ink-soft: #6b6b6b;
    --leaf-red: #a8323c;
    --leaf-orange: #e38a3c;
    --leaf-gold: #f2bc45;
  }
  * { box-sizing: border-box; margin: 0; padding: 0; }
  html, body { width: 1200px; height: 1000px; overflow: hidden; }
  body {
    background: var(--backdrop);
    font-family: "Open Sans", Arial, sans-serif;
    color: var(--ink);
    position: relative;
  }
  .card {
    position: absolute;
    left: 215px;
    width: 770px;
    height: 440px;
    background: radial-gradient(ellipse at 40% 40%, #fbf7ec 0%, var(--paper) 55%, var(--paper-edge) 100%);
    box-shadow: 0 10px 28px rgba(0,0,0,.22);
    overflow: hidden;
  }
  .card--front { top: 40px; }
  .card--back { top: 520px; }

  .autumn-branch {
    position: absolute;
    left: 0; top: 0;
    width: 420px; height: 440px;
    background:
      radial-gradient(ellipse at 40% 45%, rgba(168,50,60,.75) 0%, rgba(227,138,60,.6) 35%, rgba(242,188,69,.35) 60%, rgba(245,239,224,0) 80%);
  }
  .autumn-sprig {
    position: absolute;
    right: 40px; top: 20px;
    width: 220px; height: 100px;
    background: radial-gradient(ellipse at 40% 50%, rgba(214,160,150,.45) 0%, rgba(245,239,224,0) 70%);
  }

  .brand {
    display: flex;
    align-items: center;
    gap: 12px;
    font-weight: 800;
    color: var(--ink);
    letter-spacing: .5px;
    text-transform: uppercase;
    line-height: 1;
  }
  .brand__mark {
    width: 16px; height: 16px;
    background: var(--ink);
    flex: none;
  }
  .card--front .brand {
    position: absolute;
    left: 470px; top: 190px;
    font-size: 30px;
  }
  .social-list {
    position: absolute;
    right: 36px; top: 292px;
    display: flex;
    gap: 14px;
    list-style: none;
    font-size: 13px;
    font-weight: 600;
    color: var(--ink);
  }

  .card--back .brand {
    position: absolute;
    left: 50px; top: 200px;
    font-size: 27px;
  }
  .divider {
    position: absolute;
    left: 400px; top: 140px;
    width: 2px; height: 150px;
    background: var(--ink);
  }
  .person {
    position: absolute;
    left: 430px; top: 140px;
  }
  .person__name {
    font-size: 30px;
    font-weight: 800;
    letter-spacing: 1px;
    text-transform: uppercase;
    line-height: 1;
  }
  .person__title {
    font-size: 19px;
    font-weight: 600;
    color: var(--ink-soft);
    margin-top: 4px;
  }
  .contact-list {
    list-style: none;
    margin-top: 20px;
  }
  .contact-list li {
    display: flex;
    align-items: center;
    gap: 18px;
    font-size: 20px;
    line-height: 1.5;
  }
  .contact-list svg { width: 18px; height: 18px; flex: none; fill: var(--ink); }
</style>
</head>
<body>

<section class="card card--front" aria-label="Card front">
  <div class="autumn-branch" role="img" aria-label="Illustration of a branch with red, orange and yellow maple leaves"></div>
  <div class="autumn-sprig" role="img" aria-label="Faint illustration of a small maple sprig"></div>
  <div class="brand"><span class="brand__mark"></span>Brightwave Reach</div>
  <ul class="social-list">
    <li>Chatterly</li>
    <li>Quibber</li>
    <li>Pixlora</li>
    <li>Blinkpost</li>
  </ul>
</section>

<section class="card card--back" aria-label="Card back">
  <div class="brand"><span class="brand__mark"></span>Brightwave Reach</div>
  <div class="divider"></div>
  <div class="person">
    <p class="person__name">Daniel Moreau</p>
    <p class="person__title">Precedent</p>
    <ul class="contact-list">
      <li>
        <svg viewBox="0 0 24 24" aria-hidden="true"><path d="M6.6 10.8a15 15 0 0 0 6.6 6.6l2.2-2.2c.3-.3.7-.4 1-.2 1.1.4 2.3.6 3.6.6.6 0 1 .4 1 1V20c0 .6-.4 1-1 1A17 17 0 0 1 3 4c0-.6.4-1 1-1h3.5c.6 0 1 .4 1 1 0 1.3.2 2.5.6 3.6.1.3 0 .7-.2 1z"/></svg>
        604-555-0193
      </li>
      <li>
        <svg viewBox="0 0 24 24" aria-hidden="true"><path d="M2 5h20v14H2zm2 2v.5l8 5 8-5V7zm0 2.8V17h16V9.8l-8 5z"/></svg>
        info@brightwavereach.ca
      </li>
      <li>
        <svg viewBox="0 0 24 24" aria-hidden="true"><path d="M12 2a10 10 0 1 0 0 20 10 10 0 0 0 0-20zm6.9 9h-3a15 15 0 0 0-1.3-5.6A8 8 0 0 1 18.9 11zM12 4.1c.9 1.3 1.8 3.6 1.9 6.9h-3.8c.1-3.3 1-5.6 1.9-6.9zM9.4 5.4A15 15 0 0 0 8.1 11h-3a8 8 0 0 1 4.3-5.6zM5.1 13h3a15 15 0 0 0 1.3 5.6A8 8 0 0 1 5.1 13zm6.9 6.9c-.9-1.3-1.8-3.6-1.9-6.9h3.8c-.1 3.3-1 5.6-1.9 6.9zm2.6-1.3a15 15 0 0 0 1.3-5.6h3a8 8 0 0 1-4.3 5.6z"/></svg>
        www.brightwavereach.ca
      </li>
    </ul>
  </div>
</section>

</body>
</html>
```